Accounting firm needing business card / letterhead designed
Marcus L. Trenholm, CPA
marcus@veltrowledger.com
www.veltrowledger.com
842 E Alder Ave Perrysburg, OH 43827
419-562-0974

```html
<!DOCTYPE html>
<html lang="en">
<head>
<meta charset="utf-8">
<title>Veltrow Ledger Group – Stationery</title>
<link rel="stylesheet" href="https://fonts.googleapis.com/css2?family=Source+Sans+3:wght@400;600;700&family=Arimo:wght@400;700&display=swap">
<style>
  :root{
    --navy:#2b2570;
    --green:#8cc63f;
    --ink:#231f20;
    --grey:#6d6e71;
    --paper:#ffffff;
    --backdrop:#e9e7e3;
    --rule:#8a8aa6;
  }
  *{margin:0;padding:0;box-sizing:border-box}
  html,body{width:1200px;height:1200px;overflow:hidden}
  body{background:var(--backdrop);position:relative;font-family:"Source Sans 3",sans-serif;color:var(--ink)}

  .letterhead{position:absolute;left:54px;top:80px;width:740px;height:1045px;background:var(--paper);box-shadow:0 2px 8px rgba(0,0,0,.18)}
  .brand-name{position:absolute;font-family:"Source Sans 3",sans-serif;font-weight:700;color:var(--navy);letter-spacing:.04em;text-transform:uppercase;white-space:nowrap}
  .letterhead .brand-name{left:39px;top:70px;font-size:40px}

  .contact-block{position:absolute;font-size:15.5px;line-height:22px;color:var(--ink)}
  .contact-block .company{color:var(--navy)}
  .contact-row{display:flex;align-items:center;gap:6px}
  .icon{width:18px;height:18px;flex:none}
  .letterhead .header-contact{left:464px;top:48px;border-left:1px solid #bbb;padding-left:0}
  .header-contact .contact-row{gap:7px}

  .letter-body{position:absolute;left:39px;top:298px;width:663px;font-family:"Arimo",sans-serif;color:var(--grey)}
  .salutation{font-weight:700;font-size:17px;margin-bottom:20px}
  .letter-body p{font-size:15.5px;line-height:18px;text-align:justify;margin-bottom:18px}

  .signature{position:absolute;left:40px;top:670px;width:150px;height:72px;background:linear-gradient(90deg,#f1f1f1,#e6e6e6);border-radius:4px}

  .letterhead .footer-contact{left:39px;top:931px;line-height:23px}
  .footer-contact .contact-row{gap:5px}
  .footer-contact .contact-row .sep{width:6px}

  .web-tab{position:absolute}
  .web-tab text{font-family:"Source Sans 3",sans-serif;fill:#fff}

  .card{position:absolute;width:360px;height:205px;box-shadow:0 2px 6px rgba(0,0,0,.2);overflow:hidden}
  .card-front{left:822px;top:80px;background:var(--paper)}
  .card-front .brand-name{left:14px;top:22px;font-size:25px}
  .card-front .edge-band{position:absolute;right:0;top:0;width:44px;height:205px;background:linear-gradient(180deg,#f4f4f6,#ececef)}
  .card-holder{position:absolute;left:16px;top:101px}
  .holder-name{font-weight:700;font-size:12.5px;color:var(--navy)}
  .holder-title{font-size:8.5px;color:var(--green);margin-top:2px}
  .card-details{position:absolute;left:16px;top:138px;font-size:9px;line-height:13px}
  .card-details .company{color:var(--navy)}
  .card-details .contact-row{gap:3px;margin-top:5px}
  .card-details .icon{width:11px;height:11px}

  .card-back{left:822px;top:312px;background:var(--navy)}
  .card-back .texture{position:absolute;inset:0;background:radial-gradient(ellipse at 50% 40%,#332d80 0%,var(--navy) 70%)}
  .card-back .brand-name{left:0;right:0;top:74px;text-align:center;font-size:30px;color:#fff}
  .card-back .web{position:absolute;left:0;right:0;top:184px;display:flex;align-items:center;justify-content:center;gap:6px;font-size:9px;color:var(--green)}
  .card-back .web .line{width:58px;height:1px;background:#8d89c0}
</style>
</head>
<body>

<svg width="0" height="0" style="position:absolute">
  <defs>
    <symbol id="ic-phone" viewBox="0 0 20 20">
      <circle cx="10" cy="10" r="10" fill="var(--navy)"/>
      <path d="M6.3 5.2c.4-.3.9-.3 1.2.1l1.2 1.7c.3.4.2.9-.1 1.2l-.7.6c.5 1.2 1.4 2.2 2.6 2.8l.6-.7c.3-.4.8-.4 1.2-.2l1.7 1.1c.4.3.5.8.2 1.2l-.8 1c-.4.5-1.1.7-1.7.4-2.6-1.1-4.6-3.2-5.6-5.8-.2-.6 0-1.3.5-1.7z" fill="#fff"/>
    </symbol>
    <symbol id="ic-mail" viewBox="0 0 20 20">
      <circle cx="10" cy="10" r="10" fill="var(--navy)"/>
      <rect x="5" y="6.5" width="10" height="7" rx="1" fill="#fff"/>
      <path d="M5.4 7l4.6 3.6L14.6 7" fill="none" stroke="var(--navy)" stroke-width="1"/>
    </symbol>
  </defs>
</svg>

<section class="letterhead">
  <div class="brand-name">Veltrow Ledger</div>

  <div class="contact-block header-contact" style="border:none">
    <div class="company">Veltrow Ledger Group</div>
    <div>842 E Alder Ave Perrysburg, OH 43827</div>
    <div class="contact-row"><svg class="icon"><use href="#ic-phone"/></svg>419-562-0974</div>
    <div class="contact-row"><svg class="icon"><use href="#ic-mail"/></svg>marcus@veltrowledger.com</div>
  </div>

  <div class="letter-body">
    <div class="salutation">Dear Mr. Harlan,</div>
    <p>Lorem Ipsum is simply dummy text of the printing and typesetting industry. Lorem Ipsum has been the industry's standard dummy text ever since the 1500s, when an unknown printer took a galley of type and scrambled it to make a type specimen book. It has survived not only five centuries, but also the leap into electronic typesetting, remaining essentially unchanged.</p>
    <p>The standard chunk of Lorem Ipsum used since the 1500s is reproduced below for those interested. Sections 1.10.32 and 1.10.33 from "de Finibus Bonorum et Malorum" by Varennus are also reproduced in their exact original form, accompanied by English versions from the 1914 translation by H. Dalworth</p>
    <p>Lorem Ipsum is simply dummy text of the printing and typesetting industry. Lorem Ipsum has been the industry's standard dummy text ever since the 1500s, when an unknown printer took a galley of type and scrambled it to make a type specimen book. It has survived not only five centuries, but also the leap into electronic typesetting, remaining essentially unchanged. It was popularised in the</p>
  </div>

  <div class="signature" role="img" aria-label="Handwritten signature of the sender"></div>

  <div class="contact-block footer-contact">
    <div class="company">Veltrow Ledger Group</div>
    <div>842 E Alder Ave Perrysburg, OH 43827</div>
    <div class="contact-row"><svg class="icon"><use href="#ic-phone"/></svg>419-562-0974<span class="sep"></span><svg class="icon"><use href="#ic-mail"/></svg>marcus@veltrowledger.com</div>
  </div>

  <svg class="web-tab" style="left:0;top:990px" width="740" height="32" viewBox="0 0 740 32">
    <line x1="39" y1="16" x2="740" y2="16" stroke="var(--rule)" stroke-width="1"/>
    <polygon points="526,1 690,1 700,16 690,31 526,31 516,16" fill="var(--navy)"/>
    <text x="608" y="21" font-size="15.5" text-anchor="middle">www.veltrowledger.com</text>
  </svg>
</section>

<section class="card card-front">
  <div class="edge-band" role="img" aria-label="Faint large brand lettering along the card edge"></div>
  <div class="brand-name">Veltrow Ledger</div>
  <div class="card-holder">
    <div class="holder-name">Marcus L. Trenholm</div>
    <div class="holder-title">CPA</div>
  </div>
  <div class="card-details">
    <div class="company">Veltrow Ledger Group</div>
    <div>842 E Alder Ave Perrysburg, OH 43827</div>
    <div class="contact-row"><svg class="icon"><use href="#ic-phone"/></svg>419-562-0974&nbsp;<svg class="icon"><use href="#ic-mail"/></svg>marcus@veltrowledger.com</div>
  </div>
  <svg class="web-tab" style="left:0;top:176px" width="360" height="22" viewBox="0 0 360 22">
    <line x1="16" y1="11" x2="360" y2="11" stroke="var(--rule)" stroke-width=".8"/>
    <polygon points="230,1 330,1 337,11 330,21 230,21 224,11" fill="var(--navy)"/>
    <text x="281" y="14.5" font-size="9" text-anchor="middle">www.veltrowledger.com</text>
  </svg>
</section>

<section class="card card-back">
  <div class="texture" role="img" aria-label="Faint dotted world map texture in navy tones"></div>
  <div class="brand-name">Veltrow Ledger</div>
  <div class="web"><span class="line"></span>www.veltrowledger.com<span class="line"></span></div>
</section>

</body>
</html>
```